Shopping center investment profile

We need to design a two-page 8.5" x 11" brochure that can be used as a template for profiling our shopping centers and demonstrating our track record to investors.

Our company (QLM Real Estate Investments) owns retail shopping centers in the southwestern United States. Our website is www.qlmvx.example, but we will be redesigning and modernizing the website and logo in the near future, so please do not use the color schemes or framework of the website for the brochure.

Our investors are institutional and high net worth investors who typically have an existing relationship with our company. They are determining whether to invest multi-millions of dollars in a shopping center opportunity, so the brochure needs to be professional, very high quality and provide key information about the specific property.
Updates

Additional guidance on color scheme:

We would like to see a Blue (something like Hex #5A61BC) and Gold (Hex #EDB215) or (Hex #DDA24B) color scheme with some Black accents 

Thank you!

Target Market(s)

Our target audiences are institutional investors, high net-worth individuals, financial firms and medium to large commercial real estate companies.

Industry/Entity Type

Investment

Requirements
Must have
• Clean and modern look with corresponding fonts and colors.
• Incorporates the information found in the attached "Harborline Commons profile" Pages or PDF file.
• Final file design files that can be modified easily
Nice to have
• Two examples of industry brochures are attached. These are examples of the professional quality that we are looking for, not necessarily the design or format.

```html
<!DOCTYPE html>
<html lang="en">
<head>
<meta charset="utf-8">
<title>Harborline Commons Property Profile</title>
<link rel="stylesheet" href="https://fonts.googleapis.com/css2?family=Arimo:wght@700&family=Barlow:wght@500&family=Questrial&family=Ubuntu:wght@400;500&display=swap">
<style>
:root{
  --purple:#5a479a;
  --purple-title:#5b4aa0;
  --lavender:#a79fd6;
  --lavender-soft:#b9b4de;
  --tab:#9d97d0;
  --slate:#6f6f71;
  --slate-line:#9a97c4;
  --silver:#c9c9cb;
  --silver-line:#f2f2f4;
  --grey-text:#a5a5a7;
  --ink:#3a3a3c;
  --white:#ffffff;
}
*{margin:0;padding:0;box-sizing:border-box}
html,body{width:887px;height:1200px;overflow:hidden;background:var(--white)}
.sheet{position:relative;width:887px;height:1200px;background:var(--white);font-family:"Questrial",sans-serif;color:var(--ink)}
.hero{position:absolute;left:0;top:0;width:887px;height:428px;
  background:linear-gradient(180deg,#4d86c9 0%,#9cc2e6 30%,#c98a5f 52%,#d9b68a 70%,#6e6c70 88%,#505055 100%)}
.rule-top{position:absolute;left:0;top:428px;width:887px;height:6px;background:var(--lavender-soft)}
.address-band{position:absolute;left:0;top:434px;width:887px;height:46px;background:var(--purple);
  color:var(--white);font-family:"Barlow",sans-serif;font-weight:500;font-size:22px;letter-spacing:.4px;
  display:flex;align-items:center;justify-content:center}
.rule-under{position:absolute;left:0;top:480px;width:887px;height:5px;background:var(--lavender-soft)}
.pointer{position:absolute;left:72px;top:485px}
.title{position:absolute;left:56px;top:513px;font-family:"Arimo",sans-serif;font-weight:700;line-height:1}
.title .name{font-size:36px;color:var(--purple-title);display:block;letter-spacing:-.3px}
.title .name em{font-style:normal;color:var(--lavender)}
.title .kind{font-size:44px;color:var(--grey-text);display:block;margin-top:14px;letter-spacing:-.3px}
.section-head{position:absolute;left:37px;width:389px;font-family:"Ubuntu",sans-serif;font-weight:500;font-size:20px;color:var(--purple-title);border-bottom:2px solid var(--tab);padding-bottom:3px}
.section-head::after{content:"";position:absolute;right:50px;bottom:-9px;border-left:9px solid transparent;border-right:9px solid transparent;border-top:8px solid var(--tab)}
.points{position:absolute;left:41px;width:390px;list-style:none;font-size:14px;line-height:15.5px}
.points li{position:absolute;left:0;padding-left:16px;width:388px}
.points.bullets li::before{content:"";position:absolute;left:0;top:5px;width:7px;height:7px;border-radius:50%;background:var(--tab)}
.points.ticks li{padding-left:23px;width:395px}
.points.ticks svg{position:absolute;left:0;top:1px}
.tab{position:absolute;left:448px;height:33px;font-family:"Ubuntu",sans-serif;font-weight:500;color:var(--white);font-size:20px;line-height:33px;padding-left:24px}
.tab-line{position:absolute;height:2px;background:var(--tab)}
.panel{position:absolute;left:448px;width:400px}
.panel.summary{top:539px;height:238px;background:var(--slate);color:var(--white)}
.panel.invest{top:833px;height:307px;background:var(--silver);color:#2b2b2d}
.notch{position:absolute;right:60px;top:0;border-left:10px solid transparent;border-right:10px solid transparent;border-top:9px solid var(--white)}
.rows{position:absolute;left:15px;right:15px;list-style:none;font-family:"Ubuntu",sans-serif;font-size:12.5px}
.rows li{display:flex;justify-content:space-between;align-items:center;padding:0 15px}
.summary .rows{top:16px;border-top:2px solid var(--slate-line)}
.summary .rows li{height:28.6px;border-bottom:2px solid var(--slate-line);font-weight:500}
.summary .rows li span:last-child{font-weight:400;color:#ecebf3}
.invest .rows{top:14px;border-top:2px solid var(--silver-line)}
.invest .rows li{height:31px;border-bottom:2px solid var(--silver-line);font-weight:500}
.total{position:absolute;left:29px;top:171px;width:334px;height:36px;background:var(--tab);color:var(--white);font-family:"Ubuntu",sans-serif;font-weight:500;font-size:12.5px;line-height:36px;padding-left:19px}
.invest .rows.lower{top:213px}
.invest .rows.lower li.structure{height:70px;align-items:flex-start;padding-top:9px;border-bottom:none}
.invest .rows .structure ul{list-style:none;line-height:15.5px}
.invest .rows .structure ul li{display:block;height:auto;border:none;padding:0}
.site{position:absolute;left:628px;top:1154px;font-family:"Questrial",sans-serif;font-size:17px;letter-spacing:2.6px;color:var(--purple-title);display:flex;align-items:center;gap:6px}
.rule-bottom{position:absolute;left:0;top:1180px;width:887px;height:20px;background:var(--lavender-soft)}
</style>
</head>
<body>
<main class="sheet">
  <div class="hero" role="img" aria-label="Rendering of the shopping center storefronts with tiled roofs, signage, trees and parked cars"></div>
  <div class="rule-top"></div>
  <header class="address-band">SWC OF ALDER RD AND MERIDIAN RD LARKFIELD, ARIZONA</header>
  <div class="rule-under"></div>
  <svg class="pointer" width="42" height="20" viewBox="0 0 42 20"><polygon points="0,0 42,0 21,20" fill="var(--lavender-soft)"/></svg>

  <h1 class="title"><span class="name">Harborline <em>Commons</em></span><span class="kind">Property Profile</span></h1>

  <h2 class="section-head" style="top:628px">Opportunity</h2>
  <ul class="points bullets" style="top:671px">
    <li style="top:0">Bank owned property with attractive purchase price</li>
    <li style="top:30px">Strong relationship with seller’s broker and decision makers</li>
    <li style="top:77px">Redevelopment upside with management and leasing</li>
    <li style="top:108px">No major renovations required</li>
    <li style="top:139px">Larkfield location has very strong population, education and income demographics</li>
    <li style="top:185px">Adjacent to premier 2,500-residence master planned community of Willow Crest Lakes</li>
    <li style="top:231px">Strong employment area with the new Northgate Medical hospital and the adjacent Riverside Cancer center</li>
  </ul>

  <h2 class="section-head" style="top:948px">Results</h2>
  <ul class="points ticks" style="top:993px">
    <li style="top:0"><svg width="18" height="16" viewBox="0 0 18 16"><rect x="1" y="3" width="12" height="12" fill="none" stroke="var(--purple-title)" stroke-width="1.6"/><path d="M4 8l3 4 9-11" fill="none" stroke="var(--purple-title)" stroke-width="2.4"/></svg>Stabilized the shopping center within three years, producing excellent results for investors</li>
    <li style="top:46px"><svg width="18" height="16" viewBox="0 0 18 16"><rect x="1" y="3" width="12" height="12" fill="none" stroke="var(--purple-title)" stroke-width="1.6"/><path d="M4 8l3 4 9-11" fill="none" stroke="var(--purple-title)" stroke-width="2.4"/></svg>Transformed the center into a vibrant destination that the surrounding community is excited about</li>
    <li style="top:92px"><svg width="18" height="16" viewBox="0 0 18 16"><rect x="1" y="3" width="12" height="12" fill="none" stroke="var(--purple-title)" stroke-width="1.6"/><path d="M4 8l3 4 9-11" fill="none" stroke="var(--purple-title)" stroke-width="2.4"/></svg>Transitioned legacy tenants to upgrade the business operators</li>
    <li style="top:138px"><svg width="18" height="16" viewBox="0 0 18 16"><rect x="1" y="3" width="12" height="12" fill="none" stroke="var(--purple-title)" stroke-width="1.6"/><path d="M4 8l3 4 9-11" fill="none" stroke="var(--purple-title)" stroke-width="2.4"/></svg>Reduced the shopping center’s operating expenses by replacing vendors and appealing property taxes</li>
  </ul>

  <svg style="position:absolute;left:448px;top:500px" width="160" height="33" viewBox="0 0 160 33"><polygon points="0,0 138,0 155,33 0,33" fill="var(--tab)"/></svg>
  <div class="tab" style="top:500px">Summary</div>
  <div class="tab-line" style="left:600px;top:531px;width:248px"></div>
  <section class="panel summary">
    <div class="notch"></div>
    <ul class="rows">
      <li><span>Property Type</span><span>Shopping Center</span></li>
      <li><span>Size</span><span>79,490 sq ft</span></li>
      <li><span>Purchased</span><span>April 2011</span></li>
      <li><span>Total Investment</span><span>$X,XXX,XXX</span></li>
      <li><span>Purchase Occupancy</span><span>8.39%</span></li>
      <li><span>Current Occupancy</span><span>97.29%</span></li>
      <li><span>Projected 5-year IRR (Unleveraged)</span><span>XX.XX%</span></li>
    </ul>
  </section>

  <svg style="position:absolute;left:448px;top:793px" width="290" height="33" viewBox="0 0 290 33"><polygon points="0,0 262,0 282,33 0,33" fill="var(--tab)"/></svg>
  <div class="tab" style="top:793px">Investment Information</div>
  <div class="tab-line" style="left:725px;top:824px;width:123px"></div>
  <section class="panel invest">
    <div class="notch"></div>
    <ul class="rows">
      <li><span>Purchase Price</span><span>$X,XXX,XXX</span></li>
      <li><span>Sponsor Acquisition Fee</span><span>$XX,XXX</span></li>
      <li><span>Painting and Landscape</span><span>$XXX,XXX</span></li>
      <li><span>TI/LC Reserve</span><span>$X,XXX,XXX</span></li>
      <li><span>Operating Expenses</span><span>$XXX,XXX</span></li>
    </ul>
    <div class="total">Total Cash Investment</div>
    <ul class="rows lower">
      <li><span>Investor / Sponsor Split</span><span>XX% / XX%</span></li>
      <li class="structure"><span>Structure</span>
        <ul><li>• Cash Flow Pari Passu</li><li>• Acquisition Fee</li><li>• Management Fee</li></ul>
      </li>
    </ul>
  </section>

  <div class="site"><svg width="13" height="13" viewBox="0 0 13 13"><circle cx="6.5" cy="6.5" r="5.5" fill="none" stroke="#777" stroke-width="1"/><ellipse cx="6.5" cy="6.5" rx="2.5" ry="5.5" fill="none" stroke="#777" stroke-width="1"/><line x1="1" y1="6.5" x2="12" y2="6.5" stroke="#777" stroke-width="1"/></svg>www.qlmvx.example</div>
  <div class="rule-bottom"></div>
</main>
</body>
</html>
```